Corvane Holdings , new business card design

investment firm with corporate clients . need double sided business card , vertical and horizontal options ,logo must be clear. prefer pantone colors only and sharp design. website also www.corvane.ae

Khalid Bin Tarrafi
Managing Director
Tel. +971 4 387 2940
Mobile +971 50 518 2403
khalid@corvane.ae
Q-Span Plaza, officw 18-B07, Warqa Gardens, Dubai

Contact Information for Business Card

Khalid Bin Tarrafi
Managing Director

Font styles to use
Serif

Colors

Designer to choose colors to be used in the design.

```html
<!DOCTYPE html>
<html lang="en">
<head>
<meta charset="utf-8">
<title>Corvane Holdings – Business Card</title>
<link rel="stylesheet" href="https://fonts.googleapis.com/css2?family=Jost:wght@300;400;500&display=swap">
<style>
  :root {
    --backdrop: #2b2b2d;
    --card-blue: #477099;
    --ink-blue: #3c6a9a;
    --ink-dark: #2f3236;
    --ink-grey: #4a4d52;
    --swoosh-grey: #55585c;
    --paper: #ffffff;
  }
  * { margin: 0; padding: 0; box-sizing: border-box; }
  html, body {
    width: 1200px; height: 780px; overflow: hidden;
    background: var(--backdrop);
    font-family: "Jost", sans-serif;
  }
  .canvas { position: relative; width: 1200px; height: 780px; }
  .card {
    position: absolute;
    width: 540px; height: 309px;
    box-shadow: 0 12px 28px rgba(0,0,0,.45);
    overflow: hidden;
  }
  .card--front { left: 50px; top: 150px; background: var(--card-blue); }
  .card--back { left: 610px; top: 320px; background: var(--paper); }

  .wordmark {
    font-weight: 400;
    text-transform: uppercase;
    letter-spacing: .22em;
    line-height: 1;
    white-space: nowrap;
  }
  .card--front .wordmark {
    position: absolute; left: 0; right: 0; top: 50%;
    transform: translateY(-50%);
    text-align: center;
    color: var(--paper);
    font-size: 30px;
  }

  .card__swoosh { position: absolute; inset: 0; }
  .card--back .wordmark {
    position: absolute; left: 36px; top: 116px;
    color: var(--ink-dark);
    font-size: 16px;
  }
  .card__divider {
    position: absolute; left: 306px; top: 52px;
    width: 2px; height: 136px;
    background: var(--ink-blue);
  }
  .contact {
    position: absolute; left: 322px; top: 52px;
    color: var(--ink-grey);
    font-size: 12px; line-height: 1.35;
  }
  .contact__name {
    color: var(--ink-blue); font-weight: 500;
    font-size: 13.5px; text-transform: uppercase; letter-spacing: .02em;
  }
  .contact__title { margin-bottom: 9px; }
  .contact__address { margin-bottom: 7px; }
  .contact__row { display: flex; align-items: center; gap: 8px; }
  .contact__row svg { width: 9px; height: 9px; flex: none; }
</style>
</head>
<body>
<main class="canvas">
  <section class="card card--front" aria-label="Card front">
    <div class="wordmark">Corvane Holdings</div>
  </section>

  <section class="card card--back" aria-label="Card back">
    <svg class="card__swoosh" viewBox="0 0 540 309" preserveAspectRatio="none" aria-hidden="true">
      <path d="M0 262 C140 238 380 250 540 222 L540 309 L0 309 Z" fill="var(--swoosh-grey)"/>
      <path d="M0 270 C145 246 382 256 540 229 L540 309 L0 309 Z" fill="var(--paper)"/>
      <path d="M0 274 C150 250 384 260 540 234 L540 309 L0 309 Z" fill="var(--card-blue)"/>
    </svg>

    <div class="wordmark">Corvane Holdings</div>
    <div class="card__divider"></div>

    <div class="contact">
      <div class="contact__name">Khalid Bin Tarrafi</div>
      <div class="contact__title">Managing Director</div>
      <div class="contact__address">Q-Span Plaza, officw 18-B07,<br>Warqa Gardens, Dubai</div>
      <div class="contact__row">
        <svg viewBox="0 0 10 10" aria-hidden="true"><path d="M2 1 L4 1 L4.6 3 L3.4 3.8 Q4.4 5.8 6.2 6.6 L7 5.4 L9 6 L9 8 Q9 9 8 9 Q1 8.5 1 2 Q1 1 2 1 Z" fill="var(--ink-blue)"/></svg>
        <span>+971 4 387 2940</span>
      </div>
      <div class="contact__row">
        <svg viewBox="0 0 10 10" aria-hidden="true"><rect x="2.5" y="0.5" width="5" height="9" rx="1" fill="none" stroke="var(--ink-blue)" stroke-width="1.2"/><circle cx="5" cy="7.8" r=".6" fill="var(--ink-blue)"/></svg>
        <span>+971 50 518 2403</span>
      </div>
      <div class="contact__row">
        <svg viewBox="0 0 10 10" aria-hidden="true"><rect x="0.8" y="2" width="8.4" height="6" fill="none" stroke="var(--ink-blue)" stroke-width="1.1"/><path d="M1 2.3 L5 5.4 L9 2.3" fill="none" stroke="var(--ink-blue)" stroke-width="1.1"/></svg>
        <span>khalid@corvane.ae</span>
      </div>
    </div>
  </section>
</main>
</body>
</html>
```